Estate Agent Board Design

Most eye-catching, elegant estate agent board
Company logo should stand out
Korvimark & TREG should be small but visible.

On the board must be:

"FOR SALE"
logos
website zhbproperties.co.uk
tel number 01632 960418

It Company

```html
<!DOCTYPE html>
<html lang="en">
<head>
<meta charset="utf-8">
<title>zhb Sales &amp; Lettings – For Sale Board</title>
<link href="https://fonts.googleapis.com/css2?family=Montserrat:wght@500;700;800&display=swap" rel="stylesheet">
<style>
  :root {
    --page-bg: #ececec;
    --frame: #6f6f6f;
    --board-bg: #d8eec6;
    --brand-dark: #0f4a1f;
    --brand-mid: #1b6b30;
    --text-light: #ffffff;
    --badge-blue: #1d3f8f;
    --badge-gold: #f2b705;
    --badge-dark: #101820;
    --web-text: #2a3a2a;
  }
  * { margin: 0; padding: 0; box-sizing: border-box; }
  html, body {
    width: 1200px; height: 900px; overflow: hidden;
    background: var(--page-bg);
    font-family: "Montserrat", Arial, sans-serif;
  }
  .board {
    position: absolute; left: 287px; top: 35px;
    width: 626px; height: 830px;
    background: var(--board-bg);
    border: 8px solid var(--frame);
  }
  .brand {
    position: absolute; left: 56px; top: 100px;
    display: flex; align-items: flex-start;
  }
  .brand-mark {
    width: 196px; height: 196px;
    background: var(--brand-dark);
  }
  .brand-text { margin-left: 16px; display: flex; flex-direction: column; }
  .brand-name {
    font-weight: 800; font-size: 170px; line-height: 150px;
    letter-spacing: -6px; color: var(--brand-dark);
  }
  .brand-tagline {
    font-weight: 700; font-size: 27px; color: var(--brand-dark);
    margin-top: 14px; letter-spacing: 0.2px;
  }
  .status-band {
    position: absolute; left: 0; right: 0; top: 402px; height: 119px;
    background: var(--brand-mid);
    display: flex; align-items: center; justify-content: center;
  }
  .status-text {
    font-weight: 800; font-size: 76px; color: var(--text-light); letter-spacing: 2px;
  }
  .phone-band {
    position: absolute; left: 0; right: 0; top: 521px; height: 94px;
    background: var(--brand-dark);
    display: flex; align-items: center; justify-content: center; gap: 14px;
  }
  .phone-number {
    font-weight: 800; font-size: 40px; color: var(--text-light); letter-spacing: 2px;
  }
  .accreditations {
    position: absolute; left: 0; right: 0; top: 690px;
    display: flex; justify-content: center; gap: 14px;
  }
  .badge { width: 70px; height: 70px; }
  .badge-korvimark { background: var(--badge-dark); border-radius: 10px; }
  .badge-treg { background: var(--badge-blue); border-radius: 50%; border: 5px solid var(--badge-gold); }
  .website {
    position: absolute; left: 0; right: 0; top: 790px;
    text-align: center; font-weight: 500; font-size: 23px;
    letter-spacing: 3px; color: var(--web-text);
  }
</style>
</head>
<body>
  <main class="board">
    <div class="brand">
      <div class="brand-mark"></div>
      <div class="brand-text">
        <span class="brand-name">zhb</span>
        <span class="brand-tagline">SALES &amp; LETTINGS</span>
      </div>
    </div>

    <div class="status-band">
      <span class="status-text">FOR SALE</span>
    </div>

    <div class="phone-band">
      <svg class="phone-icon" width="30" height="38" viewBox="0 0 24 30" aria-hidden="true">
        <path d="M6 2 L10 2 L11 9 L8 11 C9 16 11 20 14 23 L17 21 L22 24 L21 28 C12 28 3 17 3 6 Z" fill="#ffffff"/>
      </svg>
      <span class="phone-number">01632 960418</span>
    </div>

    <div class="accreditations">
      <div class="badge badge-korvimark" aria-label="Korvimark accreditation"></div>
      <div class="badge badge-treg" aria-label="TREG accreditation"></div>
    </div>

    <p class="website">www.zhbproperties.co.uk</p>
  </main>
</body>
</html>
```